Web Site Mock Up's for a Dog Food Business

We are a supplier of bespoke dog food. We tailor our dog food to meet the dogs needs.We are looking for ideas (mock ups) of design ideas for our new web site - Just mock ups - web site will follow if we are happy with the mock ups.I have included our logo (PSD file). I have also included a rough (please don’t copy) home page with the information we would ideally like on the page. Note the page will have sliders at the top, we have done two example sliders, and included a video to be included.I have also enclosed the questions we need to find out in order to develop a dogs food.I would like to see a home page, and a tell us about your dog page.Would like mock ups as PSD files, so we can play around with.I am open to ideas and better designs. DO NOT JUST COPY MY LAYOUTSome of our competitors sites include www.tails.comwww.paws.comwww.parcelpet.comwww.growlingtums.co.ukI want a clean, bright easy to navigate site. Happy to play around with colours - doesn’t have to be the browns I have used. Happy to use both infographics and photo of real dogs, but I do want site to look like the best food available for dogs.Web site will be a database driven site, with around 10 -15 pages plus about 60 dynamic database driven pages of products (all same layout )Look forward to receiving your ideas.

```html
<!DOCTYPE html>
<html lang="en">
<head>
<meta charset="utf-8">
<title>Kibblecrest – Bespoke Dog Food</title>
<link href="https://fonts.googleapis.com/css2?family=Open+Sans:wght@400;600;700&display=swap" rel="stylesheet">
<style>
:root{
  --brown:#45220f;
  --brown-dark:#3a1c0c;
  --ink:#222;
  --text:#555;
  --line:#c9c9c9;
  --soft:#f4f4f4;
  --white:#fff;
}
*{box-sizing:border-box;margin:0;padding:0}
html,body{width:1200px;height:3939px;overflow:hidden}
body{font-family:'Open Sans',sans-serif;color:var(--ink);background:var(--white);position:relative}
.btn{position:absolute;display:flex;align-items:center;justify-content:center;border:3px solid var(--brown);border-radius:40px;font-weight:700;font-size:15px;letter-spacing:.3px;color:var(--ink);background:var(--white);text-transform:uppercase}

/* header */
.site-header{position:absolute;left:0;top:0;width:1200px;height:113px;background:var(--white)}
.brand{position:absolute;left:110px;top:30px;display:flex;align-items:center;gap:10px;font-weight:700;font-size:17px;color:var(--brown)}
.brand-dot{width:22px;height:22px;border-radius:50%;background:var(--brown)}
.main-nav{position:absolute;left:320px;top:45px;display:flex;gap:24px;font-size:15px;font-weight:600;color:var(--ink)}
.login{position:absolute;left:988px;top:35px;width:100px;height:46px;border-radius:24px;background:var(--brown);color:var(--white);font-weight:700;font-size:15px;display:flex;align-items:center;justify-content:center;gap:7px}

/* hero */
.hero{position:absolute;left:0;top:113px;width:1200px;height:564px;background:linear-gradient(90deg,#f1f1f1 0%,#ececec 45%,#e2ddd6 100%)}
.hero-photo{position:absolute;left:560px;top:0;width:640px;height:564px;background:radial-gradient(ellipse at 55% 45%,#b5824f 0%,#9e7350 25%,#cfc7bd 60%,#e6e3df 100%)}
.hero-title{position:absolute;left:110px;top:128px;width:480px;font-size:43px;line-height:61px;font-weight:600;color:#1e1e1e}
.hero .btn{left:110px;top:360px;width:268px;height:62px}
.play{position:absolute;left:570px;top:396px;width:58px;height:58px;border-radius:50%;background:#2a2a2a}
.hero-arrow{position:absolute;top:258px}

/* how it works */
.how{position:absolute;left:0;top:677px;width:1200px;height:478px}
.section-title{position:absolute;left:0;width:1200px;text-align:center;font-weight:600;font-size:42px;line-height:57px;color:#1e1e1e}
.step{position:absolute;top:158px;width:260px;text-align:center}
.step-art{margin:0 auto;width:140px;height:160px;border-radius:12px;background:linear-gradient(180deg,#f3f1ef,#e7e3df)}
.step-label{margin-top:28px;font-size:20px;line-height:27px;font-weight:600;color:#222}

/* foods */
.foods{position:absolute;left:0;top:1155px;width:1200px;height:901px;background:var(--soft)}
.foods-intro{position:absolute;left:0;top:140px;width:1200px;text-align:center;font-size:14px;line-height:29px;color:var(--text)}
.foods .start{left:515px;top:237px;width:170px;height:58px}
.card{position:absolute;top:368px;width:231px;height:425px;background:var(--white);box-shadow:0 2px 8px rgba(0,0,0,.18)}
.card-photo{height:157px}
.card h3{position:absolute;left:14px;top:177px;font-size:16px;font-weight:700}
.card p{position:absolute;left:14px;top:208px;width:205px;font-size:13px;line-height:22px;color:var(--text)}
.card .btn{left:12px;top:349px;width:136px;height:40px;font-size:13px}
.slide-arrow{position:absolute;width:40px;height:40px;border-radius:50%;border:2px solid #888;display:flex;align-items:center;justify-content:center;background:var(--white)}

/* testimonial */
.reviews{position:absolute;left:0;top:2056px;width:1200px;height:354px;background:linear-gradient(180deg,#4e4a45 0%,#2f2c29 50%,#5a564f 100%)}
.reviews h2{position:absolute;left:0;top:70px;width:1200px;text-align:center;font-size:42px;font-weight:600;color:var(--white)}
.quote{position:absolute;left:300px;top:150px;width:600px;text-align:center;font-style:italic;font-size:16px;line-height:31px;color:#eee}
.reviewer{position:absolute;left:0;top:240px;width:1200px;text-align:center;font-size:19px;color:var(--white)}
.rev-arrow{position:absolute;top:158px;width:48px;height:48px;border-radius:50%;border:2px solid var(--white);display:flex;align-items:center;justify-content:center}

/* faq */
.faq{position:absolute;left:0;top:2410px;width:1200px;height:707px}
.faq-item{position:absolute;left:110px;width:977px;border:1px solid var(--line)}
.faq-q{display:flex;align-items:center;height:42px;font-size:18px;color:#222}
.faq-toggle{width:44px;height:42px;background:var(--brown);color:var(--white);display:flex;align-items:center;justify-content:center;font-size:26px;font-weight:700;margin:-1px 24px 0 -1px}
.faq-a{padding:18px 0 16px 68px;font-size:14px;color:var(--text)}
.faq .btn{left:523px;top:552px;width:154px;height:55px}

/* contact */
.contact{position:absolute;left:0;top:3117px;width:1200px;height:481px;background:var(--brown)}
.contact h2{position:absolute;left:0;top:50px;width:1200px;text-align:center;font-size:42px;font-weight:600;color:var(--white)}
.field{position:absolute;background:var(--white);font-size:13px;color:#555;padding:11px 12px}
.contact .btn{left:536px;top:362px;width:128px;height:51px;background:var(--white);border-color:var(--brown-dark);box-shadow:0 0 0 2px var(--white)}

/* footer */
.site-footer{position:absolute;left:0;top:3598px;width:1200px;height:341px;background:var(--white)}
.social{position:absolute;top:106px;width:46px;height:46px;border-radius:50%;border:2px solid #aaa}
.footer-contact{position:absolute;left:0;top:187px;width:1200px;display:flex;justify-content:center;align-items:center;gap:14px;font-size:14px;color:#444}
.footer-links{position:absolute;left:0;top:229px;width:1200px;display:flex;justify-content:center;gap:22px;font-size:14px;color:#444}
.copyright{position:absolute;left:0;top:265px;width:1200px;text-align:center;font-size:14px;color:#555}
</style>
</head>
<body>

<header class="site-header">
  <div class="brand"><span class="brand-dot"></span>kibblecrest.co.uk</div>
  <nav class="main-nav">
    <span>Home</span><span>Our Food</span><span>How it Works</span><span>Pricing</span><span>Customer Reviews</span><span>FAQ</span><span>Contact Us</span>
  </nav>
  <div class="login">
    <svg width="12" height="14" viewBox="0 0 12 14"><rect x="1" y="6" width="10" height="8" rx="1" fill="#fff"/><path d="M3 6V4a3 3 0 0 1 6 0v2" stroke="#fff" stroke-width="2" fill="none"/></svg>LOGIN
  </div>
</header>

<section class="hero">
  <div class="hero-photo" role="img" aria-label="Beagle eating from a steel dog bowl"></div>
  <h1 class="hero-title">Food unique as your dog blended using the finest ingredients</h1>
  <div class="btn">Tell us about your dog</div>
  <div class="play"><svg width="58" height="58" viewBox="0 0 58 58"><path d="M23 18l18 11-18 11z" fill="#fff"/></svg></div>
  <svg class="hero-arrow" style="left:38px" width="26" height="44" viewBox="0 0 26 44"><path d="M22 4L6 22l16 18" stroke="#555" stroke-width="4" fill="none"/></svg>
  <svg class="hero-arrow" style="left:1138px" width="26" height="44" viewBox="0 0 26 44"><path d="M4 4l16 18L4 40" stroke="#555" stroke-width="4" fill="none"/></svg>
</section>

<section class="how">
  <h2 class="section-title" style="top:86px">How It Works</h2>
  <div class="step" style="left:96px"><div class="step-art" role="img" aria-label="Line drawing of a sitting dog"></div><div class="step-label">Tell us about your dog</div></div>
  <div class="step" style="left:469px"><div class="step-art" role="img" aria-label="Line drawing of a bowl of dog food"></div><div class="step-label">We Create Your Food</div></div>
  <div class="step" style="left:842px"><div class="step-art" role="img" aria-label="Line drawing of a delivery truck"></div><div class="step-label">We Delivery</div></div>
</section>

<section class="foods">
  <h2 class="section-title" style="top:60px">Our Foods</h2>
  <p class="foods-intro">We develop and create your dogs ideal food using the finest ingredients, based on your dogs requirements.<br>Our foods are developed by pet nutritionalists, approved by vets and enjoyed by all dogs.</p>
  <div class="btn start">Start now</div>

  <div class="slide-arrow" style="left:34px;top:558px"><svg width="12" height="16" viewBox="0 0 12 16"><path d="M9 2L3 8l6 6" stroke="#666" stroke-width="2" fill="none"/></svg></div>
  <div class="slide-arrow" style="left:1126px;top:558px"><svg width="12" height="16" viewBox="0 0 12 16"><path d="M3 2l6 6-6 6" stroke="#666" stroke-width="2" fill="none"/></svg></div>

  <article class="card" style="left:110px">
    <div class="card-photo" role="img" aria-label="Senior dog eating on grass" style="background:linear-gradient(160deg,#5f8a3a,#d9c9a6 60%,#7c9a4c)"></div>
    <h3>SENIOR FOOD</h3>
    <p>The right balance of protein and energy to help reduce joint pain, while maintaining weight to keep your dog active</p>
    <div class="btn">Tell me more</div>
  </article>
  <article class="card" style="left:360px">
    <div class="card-photo" role="img" aria-label="Adult dog eating from a blue bowl" style="background:linear-gradient(160deg,#8a6a4a,#c08a55 55%,#5a8fc2)"></div>
    <h3>ADULT FOOD</h3>
    <p>Careful balance of proteins, fats and oils, minerals, vitamins and carbohydrates are needed as an adult and differ between breeds</p>
    <div class="btn">Tell me more</div>
  </article>
  <article class="card" style="left:609px">
    <div class="card-photo" role="img" aria-label="Puppy eating from a bowl on a wooden floor" style="background:linear-gradient(160deg,#efeae4,#6b4a33 55%,#a87a55)"></div>
    <h3>PUPPY FOOD</h3>
    <p>A well balanced and nutritious range of foods to meet the needs of growing puppies of all breeds.</p>
    <div class="btn">Tell me more</div>
  </article>
  <article class="card" style="left:859px">
    <div class="card-photo" role="img" aria-label="Dry dog food kibble beside a food tin" style="background:linear-gradient(160deg,#f2f2f2,#dcdcdc 50%,#9a6a3e)"></div>
    <h3>WEIGHT CONTROL FOOD</h3>
    <p>Weight control is about still giving your dog a filling and tasty food that will satisfy your dogs appetite whilst keeping off extra weight.</p>
    <div class="btn">Tell me more</div>
  </article>
</section>

<section class="reviews" role="img" aria-label="Two fluffy dogs on a beach at dusk">
  <h2>What our Customers Say</h2>
  <p class="quote">I have 3 dogs all on different foods. No more trips to the shops fetching massive bags of food. This works for me and my dogs love it.</p>
  <p class="reviewer">Wren with Biscuit - Harrowfield</p>
  <div class="rev-arrow" style="left:110px"><svg width="14" height="18" viewBox="0 0 14 18"><path d="M10 2L3 9l7 7" stroke="#fff" stroke-width="2.5" fill="none"/></svg></div>
  <div class="rev-arrow" style="left:1040px"><svg width="14" height="18" viewBox="0 0 14 18"><path d="M4 2l7 7-7 7" stroke="#fff" stroke-width="2.5" fill="none"/></svg></div>
</section>

<section class="faq">
  <h2 class="section-title" style="top:96px">FAQ</h2>
  <div class="faq-item" style="top:197px;border-top:none">
    <div class="faq-q"><span class="faq-toggle">-</span>At vero eos et accusamus et iusto odio dignissimos ducimus qui blanditiis?</div>
    <div class="faq-a">Nemo enim ipsam voluptatem quia voluptas sit aspernatur aut odit aut fugit, sed quia consequuntur magni dolores eos...</div>
  </div>
  <div class="faq-item" style="top:318px"><div class="faq-q"><span class="faq-toggle">+</span>At vero eos et accusamus et iusto odio dignissimos ducimus qui blanditiis?</div></div>
  <div class="faq-item" style="top:381px"><div class="faq-q"><span class="faq-toggle">+</span>At vero eos et accusamus et iusto odio dignissimos ducimus qui blanditiis?</div></div>
  <div class="faq-item" style="top:445px"><div class="faq-q"><span class="faq-toggle">+</span>At vero eos et accusamus et iusto odio dignissimos ducimus qui blanditiis?</div></div>
  <div class="btn">View more</div>
</section>

<section class="contact">
  <h2>Contact Us</h2>
  <div class="field" style="left:257px;top:144px;width:336px;height:43px">First Name</div>
  <div class="field" style="left:607px;top:144px;width:333px;height:43px">Last Name</div>
  <div class="field" style="left:257px;top:200px;width:336px;height:43px">Email Address</div>
  <div class="field" style="left:607px;top:200px;width:333px;height:43px">Phone Number</div>
  <div class="field" style="left:257px;top:255px;width:683px;height:80px">Message</div>
  <div class="btn">Submit</div>
</section>

<footer class="site-footer">
  <div class="social" style="left:547px" role="img" aria-label="Social link"></div>
  <div class="social" style="left:605px" role="img" aria-label="Social link"></div>
  <div class="footer-contact">
    <span><svg width="10" height="14" viewBox="0 0 10 14"><path d="M5 0a5 5 0 0 1 5 5c0 4-5 9-5 9S0 9 0 5a5 5 0 0 1 5-5z" fill="#333"/><circle cx="5" cy="5" r="2" fill="#fff"/></svg> Alderbrook, OR 97000, United States</span><span>|</span>
    <span><svg width="12" height="12" viewBox="0 0 12 12"><path d="M2 0l3 3-1.5 2a7 7 0 0 0 3.5 3.5L9 7l3 3-2 2C5 12 0 7 0 2z" fill="#333"/></svg> 1 555 010 0199</span><span>|</span>
    <span><svg width="14" height="10" viewBox="0 0 14 10"><rect width="14" height="10" fill="#333"/><path d="M0 0l7 6 7-6" stroke="#fff" fill="none"/></svg> info@kibblecrest.co.uk</span>
  </div>
  <div class="footer-links"><span>Help</span><span>|</span><span>FAQ</span><span>|</span><span>Support</span><span>|</span><span>Sitemap</span><span>|</span><span>Terms Of Use</span><span>|</span><span>Privacy Statement</span></div>
  <p class="copyright">Kibblecrest © 2018 All rights reserved.</p>
</footer>

</body>
</html>
```